Business Cards Needed for Innovative Healthcare Marketing Company

We are a marketing company focused on healthcare. Our company is all about rebranding yourself renewing your image and generating results. The phoenix stands for "reborn" or "rising" which we provide new brands for our clients we take their old brands and renew it with creativity and innovation. I am looking for a business card with color dimension. I have attached an example of a card I think has the look and feel of what I am trying to accomplish. I like that the card example has black and grey font colors, I like the font placement and the small logo, I really like the use of the colors on the right those are the colors of my logo. My logo is phoenix so maybe incorporating flames similar to that design. I would like the back a solid color maybe red with an opaque version of the logo and website. As a marketing company I am always open to creative liberty!

Target Market(s)

Doctors and business professionals.

Industry/Entity Type

Marketing

Contact Information for Business Card

Valcorne Health Care Marketing
Marla Tenwick- CEO
#(512)638-2974
email-marla@valcorne.com
website- valcorne.com

Font styles to use
Sans Serif

Colors
ec1f27
f37122
ffc214
fbed22
fbf289
f04a50

Requirements
Must have
• The logo and required information
Nice to have
• icons by the information
Should not have
• child like font

```html
<!DOCTYPE html>
<html lang="en">
<head>
<meta charset="utf-8">
<title>Valcorne Health Care Marketing – Business Card</title>
<link rel="stylesheet" href="https://fonts.googleapis.com/css2?family=Open+Sans:wght@300;400;700&display=swap">
<style>
  :root {
    --bg: #e9e7e5;
    --card-white: #ffffff;
    --brand-red: #9e1d22;
    --brand-orange: #f39323;
    --text-grey: #4a4a4a;
    --card-shadow: 0 3px 10px rgba(0, 0, 0, 0.25);
  }
  * { margin: 0; padding: 0; box-sizing: border-box; }
  html, body {
    width: 1200px;
    height: 987px;
    overflow: hidden;
    background: var(--bg);
    font-family: "Open Sans", Arial, sans-serif;
  }
  .canvas { position: relative; width: 1200px; height: 987px; }
  .card {
    position: absolute;
    left: 293px;
    width: 615px;
    height: 352px;
    box-shadow: var(--card-shadow);
    overflow: hidden;
  }
  .card--front { top: 125px; background: var(--card-white); }
  .card--back { top: 511px; background: var(--brand-red); }

  .brand { position: absolute; display: flex; align-items: center; gap: 14px; }
  .brand__dot { border-radius: 50%; flex: none; }
  .brand__name {
    font-weight: 300;
    text-transform: uppercase;
    line-height: 1.15;
    letter-spacing: 0.04em;
  }
  .card--front .brand { left: 40px; top: 52px; }
  .card--front .brand__dot { width: 96px; height: 96px; background: var(--brand-orange); }
  .card--front .brand__name { color: var(--brand-red); font-size: 30px; }
  .card--front .brand__name small { display: block; font-size: 13px; letter-spacing: 0.06em; }

  .person { position: absolute; left: 156px; top: 175px; }
  .person__name { color: var(--brand-red); font-weight: 700; font-size: 22px; line-height: 1.2; }
  .person__role { color: var(--brand-orange); font-weight: 400; font-size: 17px; line-height: 1.2; }

  .contacts { position: absolute; left: 158px; top: 238px; list-style: none; }
  .contacts li {
    display: flex; align-items: center; gap: 10px;
    height: 24.5px;
    color: var(--text-grey); font-size: 16px;
  }
  .contacts svg { width: 19px; height: 19px; flex: none; }

  .card--back .brand {
    left: 0; right: 0; top: 88px;
    flex-direction: column; gap: 18px; text-align: center;
  }
  .card--back .brand__dot { width: 86px; height: 86px; background: var(--card-white); }
  .card--back .brand__name { color: var(--card-white); font-size: 34px; }
  .card--back .brand__name small { display: block; font-size: 13px; letter-spacing: 0.06em; }
</style>
</head>
<body>
<main class="canvas">
  <section class="card card--front" aria-label="Business card front">
    <div class="brand">
      <span class="brand__dot"></span>
      <p class="brand__name">Valcorne<small>Health Care Marketing</small></p>
    </div>
    <div class="person">
      <p class="person__name">Marla Tenwick</p>
      <p class="person__role">CEO</p>
    </div>
    <ul class="contacts">
      <li>
        <svg viewBox="0 0 20 20" aria-hidden="true"><circle cx="10" cy="10" r="10" fill="#9e1d22"/><path d="M6.5 5.2l2 2-1 1.3c.8 1.6 2 2.8 3.6 3.6l1.3-1 2 2-1.2 1.5c-3.7-.6-6.5-3.4-7.1-7.1z" fill="#fff"/></svg>
        (512)638-2974
      </li>
      <li>
        <svg viewBox="0 0 20 20" aria-hidden="true"><circle cx="10" cy="10" r="10" fill="#9e1d22"/><rect x="5" y="6.5" width="10" height="7" fill="#fff"/><path d="M5 6.5l5 4 5-4" fill="none" stroke="#9e1d22" stroke-width="1"/></svg>
        marla@valcorne.com
      </li>
      <li>
        <svg viewBox="0 0 20 20" aria-hidden="true"><circle cx="10" cy="10" r="10" fill="#9e1d22"/><circle cx="10" cy="10" r="5" fill="none" stroke="#fff" stroke-width="1.4"/><path d="M5 10h10M10 5c-2.5 3-2.5 7 0 10M10 5c2.5 3 2.5 7 0 10" fill="none" stroke="#fff" stroke-width="1"/></svg>
        www.valcorne.com
      </li>
    </ul>
  </section>

  <section class="card card--back" aria-label="Business card back">
    <div class="brand">
      <span class="brand__dot"></span>
      <p class="brand__name">Valcorne<small>Health Care Marketing</small></p>
    </div>
  </section>
</main>
</body>
</html>
```